Online media outlet needs a blog and logo

A new online blog platform is being established in the UK. The blog will be very similar in layout to www.quorvel.co. It will need to have a main story slider showing three slides and block tiles beneath the slider for additional tiles.

The blog platform will be called 'Tandrel Brisk' and will also need a professional looking logo design for the name.

The website should be designed in Word Press.

Industry/Entity Type

Media

Logo Text

Tandrel Brisk

Coding

Coded - Design and coding required

Number of Pages Required

3 page

Font styles to use
Other font styles liked:
• Helvetica

Requirements
Must have
• A slider showing three slides. Be similar to Quor V (see previous comment). Be Word Press compatible.

```html
<!DOCTYPE html>
<html lang="en">
<head>
<meta charset="utf-8">
<title>Tandrel Brisk</title>
<link rel="stylesheet" href="https://fonts.googleapis.com/css2?family=Arimo:wght@400;700&display=swap">
<style>
:root{
  --ink:#111;
  --black:#000;
  --white:#fff;
  --paper:#fff;
  --navbar:#e4e4e4;
  --nav-text:#777;
  --line:#dcdcdc;
  --body-text:#666;
  --chip:#fff;
  --share:#e9e9e9;
  --field-text:#aaa;
}
*{box-sizing:border-box;margin:0;padding:0}
html,body{width:1200px;height:2624px;overflow:hidden;background:var(--paper);font-family:"Arimo",Helvetica,Arial,sans-serif;color:var(--ink)}
.canvas{position:relative;width:1200px;height:2624px}
.abs{position:absolute}

/* header */
.site-header{left:0;top:0;width:1200px;height:63px;background:var(--black)}
.brand{left:194px;top:19px;color:var(--white);font-size:21px;letter-spacing:.5px}
.search-icon{left:812px;top:24px}
.header-share{left:846px;top:21px;display:flex;gap:7px}
.header-share span{width:20px;height:20px;background:var(--white)}
.menu-label{left:978px;top:25px;color:var(--white);font-size:11px;letter-spacing:.5px}
.menu-icon{left:1017px;top:22px}

/* hero */
.hero{left:0;top:63px;width:1200px;height:453px;background:linear-gradient(180deg,#6b5a3a 0%,#c08a3c 22%,#7a5a3a 42%,#4a3a30 70%,#2e2622 100%)}
.hero-tag{left:194px;top:334px;background:var(--chip);color:var(--ink);font-size:11px;font-weight:700;padding:3px 8px;letter-spacing:.3px}
.hero-title{left:194px;top:362px;color:var(--white);font-size:26px;font-weight:700;line-height:37px;text-transform:uppercase;width:520px}
.hero-more{left:198px;top:447px;color:var(--white);font-size:11px;font-weight:700}
.hero-dots{left:866px;top:478px;display:flex;gap:8px}
.hero-dots span{width:24px;height:3px;background:rgba(255,255,255,.45)}
.hero-dots span.active{background:var(--white)}

/* nav */
.main-nav{left:0;top:516px;width:1200px;height:52px;background:var(--navbar)}
.main-nav a,.footer-nav a{position:absolute;transform:translateX(-50%);font-size:10px;text-decoration:none;letter-spacing:.4px;text-transform:uppercase;white-space:nowrap}
.main-nav a{top:20px;color:var(--nav-text)}

/* tiles */
.photo-tile{overflow:hidden}
.photo-tile .tile-label{position:absolute;left:16px;top:16px;color:var(--white);font-size:10px;font-weight:700;text-transform:uppercase}
.photo-tile .tile-label.chip{background:var(--chip);color:var(--ink);padding:3px 7px;left:14px;top:14px}
.photo-tile .tile-title{position:absolute;left:14px;bottom:30px;right:40px;color:var(--white);font-size:13px;font-weight:700;line-height:17px;text-transform:uppercase}
.photo-tile .tile-meta,.text-card .tile-meta{font-size:7.5px;font-weight:700;text-transform:uppercase;letter-spacing:.2px;white-space:nowrap}
.photo-tile .tile-meta{position:absolute;left:14px;bottom:14px;color:var(--white)}
.share{position:absolute;display:flex;gap:6px}
.share span{width:18px;height:18px;background:var(--share)}
.photo-tile .share{right:14px;top:14px}
.photo-tile.big .tile-title{font-size:14px;bottom:34px}
.photo-tile.big .tile-meta{bottom:18px}

.text-card{background:var(--white);border:1px solid var(--line);padding:18px 24px;overflow:hidden}
.text-card .tile-label{font-size:10px;font-weight:700;text-transform:uppercase;line-height:12px}
.text-card .tile-title{margin-top:10px;font-size:14px;font-weight:700;line-height:18px;text-transform:uppercase}
.text-card .excerpt{margin-top:7px;font-size:10px;line-height:16px;color:var(--body-text)}
.text-card .tile-meta{margin-top:5px;color:var(--ink);line-height:10px}
.text-card .share{position:static;margin-top:10px}

/* newsletter */
.newsletter{left:0;top:1350px;width:1200px;height:336px;background:linear-gradient(120deg,#4a2a2e 0%,#6e3038 45%,#5a2a34 70%,#7a4048 100%)}
.newsletter-brand{left:0;top:1414px;width:1200px;text-align:center;color:var(--white);font-size:38px}
.newsletter-sub{left:0;top:1475px;width:1200px;text-align:center;color:var(--white);font-size:13px;font-weight:700;text-transform:uppercase}
.newsletter-note{left:0;top:1505px;width:1200px;text-align:center;color:var(--white);font-size:8.5px;font-weight:700;text-transform:uppercase}
.field{top:1537px;height:35px;font-size:10px;text-transform:uppercase;display:flex;align-items:center;padding:0 16px}
.email-field{left:338px;width:262px;background:var(--white);color:var(--field-text)}
.freq-field{left:603px;width:119px;background:var(--white);color:var(--field-text);justify-content:space-between}
.subscribe{left:736px;width:125px;border:1px solid var(--white);color:var(--white);font-weight:700;justify-content:center}

/* footer */
.site-footer{left:0;top:2480px;width:1200px;height:144px;background:var(--black)}
.footer-nav a{top:26px;color:var(--white)}
.footer-share{left:543px;top:55px;display:flex;gap:8px}
.footer-share span{width:22px;height:22px;background:var(--white)}
.copyright{left:0;top:98px;width:1200px;text-align:center;color:var(--white);font-size:9px}
</style>
</head>
<body>
<div class="canvas">

<header class="abs site-header">
  <div class="abs brand">TANDREL BRISK</div>
  <svg class="abs search-icon" width="14" height="14" viewBox="0 0 14 14" aria-hidden="true"><circle cx="5.5" cy="5.5" r="4" fill="none" stroke="#fff" stroke-width="2"/><line x1="8.5" y1="8.5" x2="12.5" y2="12.5" stroke="#fff" stroke-width="2"/></svg>
  <div class="abs header-share"><span></span><span></span><span></span><span></span></div>
  <div class="abs menu-label">MENU</div>
  <svg class="abs menu-icon" width="22" height="18" viewBox="0 0 22 18" aria-hidden="true"><g stroke="#fff" stroke-width="1.5"><line x1="0" y1="2" x2="22" y2="2"/><line x1="0" y1="9" x2="22" y2="9"/><line x1="0" y1="16" x2="22" y2="16"/></g></svg>
</header>

<section class="abs hero" role="img" aria-label="Sunset over a historic city skyline with church towers"></section>
<div class="abs hero-tag">TOP HISTORY</div>
<h1 class="abs hero-title">What is media aliquam sed primis venenatis nisl vestibulum</h1>
<div class="abs hero-more">Read more &nbsp;›</div>
<div class="abs hero-dots"><span></span><span class="active"></span><span></span></div>

<nav class="abs main-nav">
  <a style="left:275px">Home</a><a style="left:353px">Tandrel</a><a style="left:432px">Media</a><a style="left:530px">Featured Blog</a><a style="left:635px">Gallery</a><a style="left:728px">Intermedia</a><a style="left:817px">Social</a><a style="left:909px">Contact Us</a>
</nav>

<!-- first grid -->
<article class="abs photo-tile" style="left:161px;top:582px;width:283px;height:242px;background:linear-gradient(160deg,#d8c6a8,#8a6a50 60%,#3a2e28)" role="img" aria-label="Colleagues discussing work at a laptop in an office">
  <div class="tile-label chip">News</div>
  <div class="share"><span></span><span></span><span></span></div>
  <div class="tile-title">Laoreet urna cubilia a nunc metus eu dapibus</div>
  <div class="tile-meta">Signal Digest - May 01 / 2016</div>
</article>
<article class="abs photo-tile" style="left:458px;top:582px;width:284px;height:242px;background:linear-gradient(180deg,#7eb4dc,#a9cbe2 45%,#3e5d78 80%,#1e2c3a)" role="img" aria-label="Businessman looking at a city skyline under a blue sky">
  <div class="tile-label">Investment</div>
  <div class="tile-title">Laoreet urna cubilia a nunc metus eu dapibus</div>
  <div class="tile-meta">Signal Digest - May 01 / 2016</div>
</article>
<article class="abs text-card" style="left:754px;top:582px;width:285px;height:242px">
  <div class="tile-label">Media</div>
  <div class="tile-title">Laoreet urna cubilia a nunc metus eu dapibus</div>
  <p class="excerpt">Ridiculus parturient feugiat dapibus leo laoreet penatibus parturient est tincidunt eget aenean feugiat justo eros nisl eu Adipiscing sem aliquam orci donec ad dis suspendisse ac a mus sem vestibulum a parturient nunc dolor purus consectetur nullam id A.</p>
  <div class="tile-meta">Signal Digest - May 01 / 2016</div>
  <div class="share"><span></span><span></span><span></span><span></span></div>
</article>

<article class="abs photo-tile" style="left:161px;top:840px;width:283px;height:239px;background:linear-gradient(170deg,#b9c7cf,#8c8f86 50%,#3a3a38)" role="img" aria-label="Man in a leather jacket on a phone call in a city street">
  <div class="tile-label">Title here</div>
  <div class="tile-title">Laoreet urna cubilia a nunc metus eu dapibus</div>
  <div class="tile-meta">Signal Digest - May 01 / 2016</div>
</article>
<article class="abs photo-tile" style="left:161px;top:1095px;width:283px;height:240px;background:linear-gradient(180deg,#4a5668,#2a3140 50%,#141820)" role="img" aria-label="Night city lights blended with a man's silhouette">
  <div class="tile-label">Title here</div>
  <div class="tile-title">Laoreet urna cubilia a nunc metus eu dapibus</div>
  <div class="tile-meta">Signal Digest - May 01 / 2016</div>
</article>
<article class="abs photo-tile big" style="left:458px;top:840px;width:581px;height:495px;background:linear-gradient(150deg,#a89c8c,#6e5a48 45%,#3a2c22)" role="img" aria-label="Keyboard on a wooden desk with hands holding a smartphone">
  <div class="tile-label chip">Intermedia</div>
  <div class="share"><span></span><span></span><span></span><span></span></div>
  <div class="tile-title">Ullamcorper ligula condimentum ?</div>
  <div class="tile-meta">Signal Digest - May 01 / 2016</div>
</article>

<!-- newsletter -->
<section class="abs newsletter" role="img" aria-label="Close-up of a hand in a red knitted sleeve"></section>
<div class="abs newsletter-brand">TANDREL BRISK</div>
<div class="abs newsletter-sub">Ullamcorper ligula condimentum ?</div>
<div class="abs newsletter-note">Sign up to our email</div>
<div class="abs field email-field">Enter email id</div>
<div class="abs field freq-field">Daily <svg width="10" height="6" viewBox="0 0 10 6" aria-hidden="true"><polyline points="1,1 5,5 9,1" fill="none" stroke="#aaa" stroke-width="1.2"/></svg></div>
<div class="abs field subscribe">Subscribe</div>

<!-- second grid -->
<article class="abs photo-tile" style="left:161px;top:1709px;width:283px;height:239px;background:linear-gradient(160deg,#c7b28e,#8a6e4c 50%,#4a3a2c)" role="img" aria-label="Man with glasses working on a laptop in a library">
  <div class="tile-label chip">News</div>
  <div class="share"><span></span><span></span><span></span></div>
  <div class="tile-title">Laoreet urna cubilia a nunc metus eu dapibus</div>
  <div class="tile-meta">Signal Digest - May 01 / 2016</div>
</article>
<article class="abs text-card" style="left:458px;top:1709px;width:284px;height:239px">
  <div class="tile-label">Media</div>
  <div class="tile-title">Laoreet urna cubilia a nunc metus eu dapibus</div>
  <p class="excerpt">Ridiculus parturient feugiat dapibus leo laoreet penatibus parturient est tincidunt eget aenean feugiat justo eros nisl eu Adipiscing sem aliquam orci donec ad dis suspendisse ac a mus sem vestibulum a parturient nunc dolor purus consectetur nullam id A.</p>
  <div class="tile-meta">Signal Digest - May 01 / 2016</div>
  <div class="share"><span></span><span></span><span></span><span></span></div>
</article>
<article class="abs photo-tile" style="left:754px;top:1709px;width:285px;height:239px;background:linear-gradient(160deg,#e4e2dc,#a49a8c 50%,#4a4440)" role="img" aria-label="Business team meeting around a table">
  <div class="tile-label">Investment</div>
  <div class="tile-title">Laoreet urna cubilia a nunc metus eu dapibus</div>
  <div class="tile-meta">Signal Digest - May 01 / 2016</div>
</article>

<article class="abs photo-tile" style="left:161px;top:1964px;width:283px;height:240px;background:linear-gradient(160deg,#6a7a90,#b09478 50%,#2a3656)" role="img" aria-label="Smiling businesswoman in a blue blazer">
  <div class="tile-label">Title here</div>
  <div class="tile-title">Laoreet urna cubilia a nunc metus eu dapibus</div>
  <div class="tile-meta">Signal Digest - May 01 / 2016</div>
</article>
<article class="abs text-card" style="left:161px;top:2221px;width:283px;height:242px">
  <div class="tile-label">Media</div>
  <div class="tile-title">Laoreet urna cubilia a nunc metus eu dapibus</div>
  <p class="excerpt">Ridiculus parturient feugiat dapibus leo laoreet penatibus parturient est tincidunt eget aenean feugiat justo eros nisl eu Adipiscing sem aliquam orci donec ad dis suspendisse ac a mus sem vestibulum a parturient nunc dolor purus consectetur nullam id A.</p>
  <div class="tile-meta">Signal Digest - May 01 / 2016</div>
  <div class="share"><span></span><span></span><span></span><span></span></div>
</article>
<article class="abs photo-tile big" style="left:458px;top:1964px;width:581px;height:499px;background:radial-gradient(circle at 62% 22%,#f0c27a 0%,#a86a30 22%,#3a2418 55%,#140e0c 100%)" role="img" aria-label="Crowd watching golden fireworks at night">
  <div class="tile-label chip">Intermedia</div>
  <div class="share"><span></span><span></span><span></span><span></span></div>
  <div class="tile-title">Ullamcorper ligula condimentum ?</div>
  <div class="tile-meta">Signal Digest - May 01 / 2016</div>
</article>

<footer class="abs site-footer">
  <nav class="footer-nav">
    <a style="left:275px">Home</a><a style="left:353px">Tandrel</a><a style="left:432px">Media</a><a style="left:530px">Featured Blog</a><a style="left:635px">Gallery</a><a style="left:728px">Intermedia</a><a style="left:817px">Social</a><a style="left:909px">Contact Us</a>
  </nav>
  <div class="abs footer-share"><span></span><span></span><span></span><span></span></div>
  <div class="abs copyright">All Rights Reserved. Copyrights @ 2016 company name</div>
</footer>

</div>
</body>
</html>
```